Website Design for The Elder Nook

Please design and code a new website.
Here are the sites I like best:
http://www.voyaglint.com/alternate/
http://www.wheelgiftbay.org
Please make it similar but look at the competitor site (below) for images and wording. This is NOT a car donation site. It's a senior lead placement site like https://www.kinhavenfinder.com. I just like this sites above as a lead generation sites.
Competitor site:
https://www.kinhavenfinder.com (use ideas / verbiage from this site)
Updates
Competitor site:
Coding
Coded - Design and coding required
Number of Pages Required
1 page
Look and feel
Each slider illustrates characteristics of the customer's brand and the style your logo design should communicate.

```html
<!DOCTYPE html>
<html lang="en">
<head>
<meta charset="utf-8">
<title>The Elder Nook – Homepage Layouts</title>
<link href="https://fonts.googleapis.com/css2?family=Montserrat:wght@500;600;700&family=Open+Sans:ital,wght@0,400;0,600;0,700;1,400&display=swap" rel="stylesheet">
<style>
:root{
  --blue:#0b76b6;
  --blue-dark:#0a6aa5;
  --orange:#ef8a2a;
  --orange-soft:#f29a45;
  --ink:#333a40;
  --muted:#8a8f94;
  --line:#e3e3e3;
  --stage:#f3f3f3;
  --dark:#2a2a2b;
  --white:#ffffff;
}
*{box-sizing:border-box;margin:0;padding:0}
html,body{width:944px;height:1200px;overflow:hidden;background:var(--stage)}
body{font-family:"Open Sans",Arial,sans-serif;color:var(--ink)}
.stage{position:absolute;left:0;top:0;width:1708px;height:2171px;transform:scale(.55269);transform-origin:0 0;background:var(--stage)}
.page{position:absolute;top:153px;width:632px;background:var(--white);box-shadow:0 2px 10px rgba(0,0,0,.08);overflow:hidden}
.page--form{left:152px;height:1710px}
.page--search{left:924px;height:1847px}
.abs{position:absolute}
.center{left:0;right:0;text-align:center}

/* header */
.brand{left:58px;top:14px;display:flex;align-items:center;gap:7px}
.brand__dot{width:26px;height:26px;border-radius:50%;border:2px solid var(--blue)}
.brand__name{font-family:"Montserrat",sans-serif;font-weight:600;font-size:13px;color:var(--blue)}
.hotline{left:366px;top:8px;display:flex;align-items:center;gap:5px;font-size:7px;color:var(--ink)}
.hotline__icon{width:17px;height:17px;border-radius:50%;border:1px solid var(--orange);display:flex;align-items:center;justify-content:center}
.hotline strong{font-family:"Montserrat",sans-serif;font-size:10.5px;color:var(--blue);font-weight:700}
.nav{right:59px;top:36px;display:flex;gap:10px;font-family:"Montserrat",sans-serif;font-weight:600;font-size:8px;color:var(--ink)}
.rule{left:0;right:0;height:1px;background:var(--line)}
.cities{left:55px;top:60px;display:flex;gap:10px;font-size:7.5px;color:#666}

/* hero */
.hero{left:0;top:77px;width:632px;height:335px}
.hero__photo{position:absolute;inset:0}
.hero__photo--left{background:linear-gradient(90deg,#a89a8e 0%,#c9c4bd 35%,#d8d8d6 60%,#c4c5c3 100%)}
.hero__photo--right{background:linear-gradient(90deg,#c9cbca 0%,#d6d6d4 45%,#c7bcb1 68%,#a79a8f 100%)}
.hero__curve{position:absolute;left:0;top:0}
.dots{left:0;right:0;top:279px;display:flex;justify-content:center;gap:3px}
.dots span{width:7px;height:7px;border-radius:50%;border:1px solid var(--white)}
.dots span:first-child{background:var(--white)}

.lead-form{left:361px;top:22px;width:212px;height:238px;background:rgba(118,118,118,.72)}
.lead-form h2{font-family:"Montserrat",sans-serif;font-weight:600;font-size:19px;color:var(--white);text-align:center;margin-top:12px}
.lead-form p{font-size:9px;color:var(--white);text-align:center;margin-top:5px}
.lead-form p b{font-family:"Montserrat",sans-serif;font-size:11px}
.field{position:absolute;background:var(--white);font-size:6.5px;color:#888;padding:5px 7px;height:19px}
.btn{position:absolute;border-radius:14px;font-family:"Montserrat",sans-serif;font-weight:700;color:var(--white);display:flex;align-items:center;justify-content:center}
.btn--orange{background:var(--orange)}
.btn--dark{background:var(--dark)}

.hero-text h1{font-family:"Montserrat",sans-serif;font-weight:700;font-size:25px;color:var(--white);letter-spacing:.5px}
.hero-text p{font-size:10px;color:var(--white);margin-top:9px}
.hero-text p b{font-family:"Montserrat",sans-serif;font-size:12px}
.finder{left:81px;top:113px;width:176px;height:119px;background:rgba(120,120,120,.55);border-radius:3px}
.finder h3{font-family:"Montserrat",sans-serif;font-weight:500;font-size:9.5px;color:var(--white);text-align:center;margin-top:14px}
.finder .field{left:24px;top:39px;width:155px;height:23px;padding-top:7px}

/* welcome */
.sec-title{font-family:"Montserrat",sans-serif;font-weight:700;font-size:22px;color:var(--blue);text-transform:uppercase}
.welcome__text{left:116px;width:400px;top:485px;text-align:center;font-size:7.5px;line-height:15.5px;color:var(--muted)}
.feature{top:551px;width:130px;text-align:center}
.feature__ring{width:80px;height:80px;margin:0 auto;border-radius:50%;border:1px solid var(--blue);padding:3px}
.feature__ring div{width:100%;height:100%;border-radius:50%;border:3px solid var(--blue);display:flex;align-items:center;justify-content:center}
.feature h4{font-family:"Montserrat",sans-serif;font-weight:500;font-size:9px;margin-top:10px;color:var(--ink)}
.feature p{font-size:6.8px;line-height:13.5px;color:var(--muted);margin-top:7px;padding:0 4px}

/* why */
.why{left:0;width:632px;top:749px;height:300px;background:var(--blue)}
.why h2{left:59px;top:42px;font-family:"Montserrat",sans-serif;font-weight:700;font-size:21px;color:var(--white)}
.why__intro{left:59px;top:77px;width:222px;font-size:7px;line-height:14px;color:var(--white)}
.why__item{left:59px;display:flex;align-items:center;gap:14px;font-family:"Montserrat",sans-serif;font-size:9.5px;line-height:15px;color:var(--white)}
.why__icon{width:37px;height:37px;border-radius:50%;background:var(--white);display:flex;align-items:center;justify-content:center}
.why__photo{left:316px;top:38px;width:257px;height:222px;border-radius:14px;border:3px solid var(--white);background:linear-gradient(135deg,#e7e4df 0%,#d8cfc4 45%,#a3948a 75%,#4b4a50 100%)}

/* testimonials */
.stars{font-size:11px;color:#e3b21d;letter-spacing:1px}
.quote{left:116px;width:400px;text-align:center;font-style:italic;font-size:7.8px;line-height:16px;color:#666}
.avatars{left:0;right:0;display:flex;justify-content:center;align-items:center;gap:12px}
.avatar{border-radius:50%;background:radial-gradient(circle at 50% 40%,#e6e1dc,#b7b4b6 70%,#8e92a6)}
.avatar--sm{width:40px;height:40px}
.avatar--lg{width:52px;height:52px;border:2px solid #d6eaf5}
.person{font-family:"Open Sans",sans-serif;font-size:9px;text-transform:uppercase;color:var(--ink)}
.person-role{font-size:6.8px;color:#666}

/* advisor + contact */
.band-orange{left:0;width:632px;background:linear-gradient(100deg,#ee8b30 0%,#f3a157 45%,#ef9441 70%,#ec8a2f 100%)}
.band-orange h2{font-family:"Montserrat",sans-serif;font-weight:700;font-size:22px;color:var(--white);text-transform:uppercase}
.search-bar{left:124px;top:77px;width:383px;height:30px;display:flex}
.search-bar .input{flex:1;background:var(--white);font-size:7.5px;color:#888;padding:10px 10px}
.search-bar .go{width:76px;background:var(--blue);color:var(--white);font-family:"Montserrat",sans-serif;font-weight:700;font-size:9px;display:flex;align-items:center;justify-content:center}

/* footer */
.socials{left:0;right:0;display:flex;justify-content:center;gap:5px}
.socials span{width:26px;height:26px;border-radius:50%;border:1px solid var(--orange);display:flex;align-items:center;justify-content:center}
.socials span i{width:6px;height:6px;border-radius:50%;background:var(--orange);display:block}
.foot-line{left:0;right:0;text-align:center;font-size:7px;color:#555}
.foot-line .pin{color:var(--orange)}
.footer-dark{left:0;top:1600px;width:633px;height:247px}
.footer-dark .foot-line{color:#e6e6e6}
</style>
</head>
<body>
<div class="stage">

<!-- ===== Layout A: hero with lead form ===== -->
<section class="page page--form">
  <div class="abs brand"><span class="brand__dot"></span><span class="brand__name">The Elder Nook</span></div>
  <div class="abs hotline"><span class="hotline__icon"><svg width="8" height="8" viewBox="0 0 24 24"><path fill="#ef8a2a" d="M6.6 10.8a15 15 0 0 0 6.6 6.6l2.2-2.2c.3-.3.7-.4 1-.2 1.1.4 2.3.6 3.6.6.6 0 1 .4 1 1V20c0 .6-.4 1-1 1A17 17 0 0 1 3 4c0-.6.4-1 1-1h3.5c.6 0 1 .4 1 1 0 1.3.2 2.5.6 3.6.1.3 0 .7-.2 1z"/></svg></span>Talk to a local advisor for FREE <strong>1 800 555 0142</strong></div>
  <nav class="abs nav"><span>Assisted Living</span><span>Memory Care</span><span>Nursing Homes</span><span>More Living Options</span><span>Planning &amp; Advice</span></nav>
  <div class="abs rule" style="top:55px"></div>
  <div class="abs cities"><span>New York</span><span>Los Angeles</span><span>Chicago</span><span>Dallas</span><span>Houston</span><span>Philadelphia</span><span>Miami</span><span>Atlanta</span><span>Boston</span><span>San Jose</span><span>Phoenix</span><span>Seattle</span><span>Minneapolis</span></div>
  <div class="abs rule" style="top:76px"></div>

  <div class="abs hero">
    <div class="hero__photo hero__photo--left" role="img" aria-label="Smiling senior man with a grey beard seated in a bright living room"></div>
    <div class="abs lead-form">
      <h2>The Elder Nook</h2>
      <p>Need help? Call <b>1 800 555 0142</b></p>
      <div class="field" style="left:10px;top:67px;width:93px">First Name</div>
      <div class="field" style="left:109px;top:67px;width:93px">Last Name</div>
      <div class="field" style="left:10px;top:92px;width:93px">Address</div>
      <div class="field" style="left:109px;top:92px;width:93px">Phone</div>
      <div class="field" style="left:10px;top:117px;width:192px">Email Address</div>
      <div class="field" style="left:10px;top:143px;width:192px;height:44px">Message</div>
      <div class="btn btn--orange" style="left:74px;top:198px;width:64px;height:25px;font-size:8px">SUBMIT</div>
    </div>
    <div class="abs dots"><span></span><span></span><span></span><span></span></div>
    <svg class="hero__curve" width="632" height="340" viewBox="0 0 632 340"><path d="M0 255 Q316 405 632 255 V340 H0Z" fill="#fff"/><path d="M0 258 Q316 418 632 252" fill="none" stroke="#ef8a2a" stroke-width="5"/></svg>
  </div>

  <h2 class="abs center sec-title" style="top:449px">Welcome to The Elder Nook</h2>
  <p class="abs welcome__text">Ut enim ad minima veniam, quis nostrum exercitationem ullam corporis suscipit laboriosam, nisi ut aliquid ex eacommodi consequ autem vel eum iure reprehenderit qui in ea voluptate velit esse quam nihil molestiae consequatur, vel illum qui dolorem eum fugiat quo voluptas nulla pari.</p>

  <div class="abs feature" style="left:45px"><div class="feature__ring"><div><svg width="26" height="26" viewBox="0 0 24 24"><rect x="3" y="5" width="18" height="16" rx="1" fill="none" stroke="#ef8a2a" stroke-width="2"/><path d="M3 9h18M8 3v4M16 3v4M7 12h2M11 12h2M15 12h2M7 16h2M11 16h2M15 16h2" stroke="#ef8a2a" stroke-width="2"/></svg></div></div><h4>Help scheduling tours</h4><p>Nemo enim ipsam voluptatem quia voluptas sit aspernatur aut odit aut fugit ostru.</p></div>
  <div class="abs feature" style="left:181px"><div class="feature__ring"><div><svg width="26" height="26" viewBox="0 0 24 24"><path d="M3 3h8l10 10-8 8L3 11z" fill="#ef8a2a"/><circle cx="7" cy="7" r="1.6" fill="#fff"/></svg></div></div><h4>Full details and pricing</h4><p>Nemo enim ipsam voluptatem quia voluptas sit aspernatur aut odit aut fugit ostru.</p></div>
  <div class="abs feature" style="left:318px"><div class="feature__ring"><div><svg width="24" height="24" viewBox="0 0 24 24"><circle cx="12" cy="8" r="4.5" fill="#ef8a2a"/><path d="M3 21c0-5 4-8 9-8s9 3 9 8z" fill="#ef8a2a"/></svg></div></div><h4>Dedicated local advisor</h4><p>Nemo enim ipsam voluptatem quia voluptas sit aspernatur aut odit aut fugit ostru.</p></div>
  <div class="abs feature" style="left:454px"><div class="feature__ring"><div><svg width="24" height="26" viewBox="0 0 24 24"><path d="M5 2h10l5 5v15H5z" fill="#ef8a2a"/><path d="M8 11h9M8 14h9M8 17h9" stroke="#fff" stroke-width="1.5"/></svg></div></div><h4>Hand-picked list</h4><p>Nemo enim ipsam voluptatem quia voluptas sit aspernatur aut odit aut fugit ostru.</p></div>

  <div class="abs why">
    <h2 class="abs">WHY CHOOSE US</h2>
    <p class="abs why__intro">Nemo enim ipsam voluptatem quia voluptas sit aspernatur aut odit aut fugit, sed quia consequuntur magni dolor.</p>
    <div class="abs why__item" style="top:120px"><span class="why__icon"><svg width="16" height="16" viewBox="0 0 24 24"><path d="M3 11a8 6 0 1 1 4 5l-4 2 1-4a6 6 0 0 1-1-3z" fill="none" stroke="#ef8a2a" stroke-width="2"/></svg></span><span>Advice tailored to your<br>unique situation</span></div>
    <div class="abs why__item" style="top:165px"><span class="why__icon"><svg width="16" height="16" viewBox="0 0 24 24"><circle cx="12" cy="12" r="9" fill="none" stroke="#ef8a2a" stroke-width="2"/><path d="M12 7v5h4" fill="none" stroke="#ef8a2a" stroke-width="2"/></svg></span><span>Time saving know-how<br>and resources</span></div>
    <div class="abs why__item" style="top:210px"><span class="why__icon"><svg width="14" height="16" viewBox="0 0 24 24"><path d="M12 2a7 7 0 0 0-7 7c0 5 7 13 7 13s7-8 7-13a7 7 0 0 0-7-7z" fill="#ef8a2a"/><circle cx="12" cy="9" r="2.5" fill="#fff"/></svg></span><span>Insider's tips for the area<br>near you</span></div>
    <div class="abs why__photo" role="img" aria-label="Happy senior couple embracing outdoors"></div>
  </div>

  <h2 class="abs center sec-title" style="top:1101px">Testimonials</h2>
  <div class="abs center stars" style="top:1147px">★★★★☆</div>
  <p class="abs quote" style="top:1170px">Nemo enim ipsam voluptatem quia voluptas sit aspernatur aut odit aut fugit, sed quia consequuntur magni dolores eos qui ratione voluptatem eque porro quisquam est, qui dolorem ipsum quia dt</p>
  <div class="abs avatars" style="top:1218px"><span class="avatar avatar--sm" role="img" aria-label="Client portrait"></span><span class="avatar avatar--lg" role="img" aria-label="Client portrait"></span><span class="avatar avatar--sm" role="img" aria-label="Client portrait"></span></div>
  <div class="abs center person" style="top:1286px">Martin Hale</div>
  <div class="abs center person-role" style="top:1301px">Eiusmod tempor incid</div>

  <div class="abs band-orange" style="top:1362px;height:240px" role="img" aria-label="Senior man using a tablet, tinted orange">
    <h2 class="abs center" style="top:32px">Find an advisor near you</h2>
    <div class="abs search-bar"><div class="input"><span style="color:#666">⚲</span> Enter city or postal code</div><div class="go">SEARCH</div></div>
    <svg class="abs" style="left:0;top:0" width="632" height="240" viewBox="0 0 632 240"><path d="M0 225 Q316 65 632 225 V240 H0Z" fill="#fff"/><path d="M0 222 Q316 60 632 222" fill="none" stroke="#0b76b6" stroke-width="5"/></svg>
  </div>

  <div class="abs socials" style="top:1574px"><span><i></i></span><span><i></i></span><span><i></i></span><span><i></i></span></div>
  <div class="abs foot-line" style="top:1620px"><span class="pin">●</span> Totam rem aperiam, eaque ip &nbsp;|&nbsp; <span class="pin">✆</span> 1 800 555 0142 &nbsp;|&nbsp; <span class="pin">✉</span> &nbsp;hello@theeldernook.com</div>
  <div class="abs foot-line" style="top:1644px">Help &nbsp;&nbsp;|&nbsp;&nbsp; FAQ &nbsp;&nbsp;|&nbsp;&nbsp; Support &nbsp;&nbsp;|&nbsp;&nbsp; Sitemap &nbsp;&nbsp;|&nbsp;&nbsp; Terms Of Use &nbsp;&nbsp;|&nbsp;&nbsp; Privacy Statement</div>
  <div class="abs foot-line" style="top:1667px">The Elder Nook © 2019 All rights reserved.</div>
</section>

<!-- ===== Layout B: hero with location search ===== -->
<section class="page page--search">
  <div class="abs brand"><span class="brand__dot"></span><span class="brand__name">The Elder Nook</span></div>
  <div class="abs hotline"><span class="hotline__icon"><svg width="8" height="8" viewBox="0 0 24 24"><path fill="#ef8a2a" d="M6.6 10.8a15 15 0 0 0 6.6 6.6l2.2-2.2c.3-.3.7-.4 1-.2 1.1.4 2.3.6 3.6.6.6 0 1 .4 1 1V20c0 .6-.4 1-1 1A17 17 0 0 1 3 4c0-.6.4-1 1-1h3.5c.6 0 1 .4 1 1 0 1.3.2 2.5.6 3.6.1.3 0 .7-.2 1z"/></svg></span>Talk to a local advisor for FREE <strong>1 800 555 0142</strong></div>
  <nav class="abs nav"><span>Assisted Living</span><span>Memory Care</span><span>Nursing Homes</span><span>More Living Options</span><span>Planning &amp; Advice</span></nav>
  <div class="abs rule" style="top:55px"></div>
  <div class="abs cities"><span>New York</span><span>Los Angeles</span><span>Chicago</span><span>Dallas</span><span>Houston</span><span>Philadelphia</span><span>Miami</span><span>Atlanta</span><span>Boston</span><span>San Jose</span><span>Phoenix</span><span>Seattle</span><span>Minneapolis</span></div>
  <div class="abs rule" style="top:76px"></div>

  <div class="abs hero">
    <div class="hero__photo hero__photo--right" role="img" aria-label="Smiling senior man with a grey beard seated in a bright living room"></div>
    <div class="abs hero-text" style="left:20px;width:326px;top:42px;text-align:center">
      <h1>THE ELDER NOOK</h1>
      <p>Need help? Call <b>1 800 555 0142</b></p>
    </div>
    <div class="abs finder">
      <h3>Find Senior Living Near You</h3>
      <div class="field"><span style="color:#666">⚲</span> Enter City or Postal Code</div>
      <div class="btn btn--orange" style="left:27px;top:73px;width:150px;height:25px;font-size:7.5px">START YOUR SEARCH</div>
    </div>
    <div class="abs dots"><span></span><span></span><span></span><span></span></div>
    <svg class="hero__curve" width="633" height="340" viewBox="0 0 633 340"><path d="M0 255 Q316 405 633 255 V340 H0Z" fill="#fff"/><path d="M0 258 Q316 418 633 252" fill="none" stroke="#ef8a2a" stroke-width="5"/></svg>
  </div>

  <h2 class="abs center sec-title" style="top:449px">Welcome to The Elder Nook</h2>
  <p class="abs welcome__text">Ut enim ad minima veniam, quis nostrum exercitationem ullam corporis suscipit laboriosam, nisi ut aliquid ex eacommodi consequ autem vel eum iure reprehenderit qui in ea voluptate velit esse quam nihil molestiae consequatur, vel illum qui dolorem eum fugiat quo voluptas nulla pari.</p>

  <div class="abs feature" style="left:45px"><div class="feature__ring"><div><svg width="26" height="26" viewBox="0 0 24 24"><rect x="3" y="5" width="18" height="16" rx="1" fill="none" stroke="#ef8a2a" stroke-width="2"/><path d="M3 9h18M8 3v4M16 3v4M7 12h2M11 12h2M15 12h2M7 16h2M11 16h2M15 16h2" stroke="#ef8a2a" stroke-width="2"/></svg></div></div><h4>Help scheduling tours</h4><p>Nemo enim ipsam voluptatem quia voluptas sit aspernatur aut odit aut fugit ostru.</p></div>
  <div class="abs feature" style="left:181px"><div class="feature__ring"><div><svg width="26" height="26" viewBox="0 0 24 24"><path d="M3 3h8l10 10-8 8L3 11z" fill="#ef8a2a"/><circle cx="7" cy="7" r="1.6" fill="#fff"/></svg></div></div><h4>Full details and pricing</h4><p>Nemo enim ipsam voluptatem quia voluptas sit aspernatur aut odit aut fugit ostru.</p></div>
  <div class="abs feature" style="left:318px"><div class="feature__ring"><div><svg width="24" height="24" viewBox="0 0 24 24"><circle cx="12" cy="8" r="4.5" fill="#ef8a2a"/><path d="M3 21c0-5 4-8 9-8s9 3 9 8z" fill="#ef8a2a"/></svg></div></div><h4>Dedicated local advisor</h4><p>Nemo enim ipsam voluptatem quia voluptas sit aspernatur aut odit aut fugit ostru.</p></div>
  <div class="abs feature" style="left:454px"><div class="feature__ring"><div><svg width="24" height="26" viewBox="0 0 24 24"><path d="M5 2h10l5 5v15H5z" fill="#ef8a2a"/><path d="M8 11h9M8 14h9M8 17h9" stroke="#fff" stroke-width="1.5"/></svg></div></div><h4>Hand-picked list</h4><p>Nemo enim ipsam voluptatem quia voluptas sit aspernatur aut odit aut fugit ostru.</p></div>

  <div class="abs why" style="width:633px;height:301px">
    <h2 class="abs">WHY CHOOSE US</h2>
    <p class="abs why__intro">Nemo enim ipsam voluptatem quia voluptas sit aspernatur aut odit aut fugit, sed quia consequuntur magni dolor.</p>
    <div class="abs why__item" style="top:120px"><span class="why__icon"><svg width="16" height="16" viewBox="0 0 24 24"><path d="M3 11a8 6 0 1 1 4 5l-4 2 1-4a6 6 0 0 1-1-3z" fill="none" stroke="#ef8a2a" stroke-width="2"/></svg></span><span>Advice tailored to your<br>unique situation</span></div>
    <div class="abs why__item" style="top:165px"><span class="why__icon"><svg width="16" height="16" viewBox="0 0 24 24"><circle cx="12" cy="12" r="9" fill="none" stroke="#ef8a2a" stroke-width="2"/><path d="M12 7v5h4" fill="none" stroke="#ef8a2a" stroke-width="2"/></svg></span><span>Time saving know-how<br>and resources</span></div>
    <div class="abs why__item" style="top:210px"><span class="why__icon"><svg width="14" height="16" viewBox="0 0 24 24"><path d="M12 2a7 7 0 0 0-7 7c0 5 7 13 7 13s7-8 7-13a7 7 0 0 0-7-7z" fill="#ef8a2a"/><circle cx="12" cy="9" r="2.5" fill="#fff"/></svg></span><span>Insider's tips for the area<br>near you</span></div>
    <div class="abs why__photo" role="img" aria-label="Happy senior couple embracing outdoors"></div>
  </div>

  <div class="abs band-orange" style="top:1050px;height:268px;width:633px" role="img" aria-label="Senior man using a tablet, tinted orange">
    <h2 class="abs center" style="top:38px">Contact us</h2>
    <div class="field" style="left:136px;top:80px;width:177px;height:22px">First Name</div>
    <div class="field" style="left:319px;top:80px;width:177px;height:22px">Email</div>
    <div class="field" style="left:136px;top:109px;width:177px;height:22px">Phone Number</div>
    <div class="field" style="left:319px;top:109px;width:177px;height:22px">Address</div>
    <div class="field" style="left:136px;top:138px;width:360px;height:44px">Message</div>
    <div class="btn btn--dark" style="left:276px;top:201px;width:81px;height:29px;font-size:8.5px">SUBMIT</div>
  </div>

  <h2 class="abs center sec-title" style="top:1372px">Testimonials</h2>
  <div class="abs center stars" style="top:1418px">★★★★☆</div>
  <p class="abs quote" style="top:1441px">Nemo enim ipsam voluptatem quia voluptas sit aspernatur aut odit aut fugit, sed quia consequuntur magni dolores eos qui ratione voluptatem eque porro quisquam est, qui dolorem ipsum quia dt</p>
  <div class="abs avatars" style="top:1489px"><span class="avatar avatar--sm" role="img" aria-label="Client portrait"></span><span class="avatar avatar--lg" role="img" aria-label="Client portrait"></span><span class="avatar avatar--sm" role="img" aria-label="Client portrait"></span></div>
  <div class="abs center person" style="top:1557px">Martin Hale</div>
  <div class="abs center person-role" style="top:1572px">Eiusmod tempor incid</div>

  <div class="abs footer-dark">
    <svg class="abs" style="left:0;top:0" width="633" height="247" viewBox="0 0 633 247"><path d="M0 120 Q316 -46 633 120 V247 H0Z" fill="#2a2a2b"/><path d="M0 114 Q316 -54 633 114" fill="none" stroke="#ef8a2a" stroke-width="5"/></svg>
    <div class="abs socials" style="top:105px"><span><i></i></span><span><i></i></span><span><i></i></span><span><i></i></span></div>
    <div class="abs foot-line" style="top:150px"><span class="pin">●</span> Totam rem aperiam, eaque ip &nbsp;|&nbsp; <span class="pin">✆</span> 1 800 555 0142 &nbsp;|&nbsp; <span class="pin">✉</span> &nbsp;hello@theeldernook.com</div>
    <div class="abs foot-line" style="top:174px">Help &nbsp;&nbsp;|&nbsp;&nbsp; FAQ &nbsp;&nbsp;|&nbsp;&nbsp; Support &nbsp;&nbsp;|&nbsp;&nbsp; Sitemap &nbsp;&nbsp;|&nbsp;&nbsp; Terms Of Use &nbsp;&nbsp;|&nbsp;&nbsp; Privacy Statement</div>
    <div class="abs foot-line" style="top:197px">The Elder Nook © 2019 All rights reserved.</div>
  </div>
</section>

</div>
</body>
</html>
```